IT Company that provides secure IT solutions and services to our customers

We need business cards and a logo for a new IT Solutions company just created based in Kuala Lumpur, Malaysia. But will also be serving other countries in the region. We provide secure data, voice solutions on mobile platforms. Our first offering is encrypted voice and data solutions for IOS, Android, Windows and BlackBerry devices.

Target Market(s)

large organizations Govt, Police, Defence, Anti-corruption, Legal, highly regulated industries such as Health-care, Financial, Banking, Insurance,

Industry/Entity Type

Information Technology

Contact Information for Business Card

VelmoraNet (Logo - colour is ORVEX blue)Roshan Adeel Managing Director Velmora Net Sdn. Bhd.5th Floor, Block D, Wisma PLB,No.14 Jalan Seri Melor,50470, Kuala LumpurMalaysia

Font styles to use
Sans Serif

Colors
3176b5
ec1f27
fbed22

Requirements
Must have
• VelmoraNet all in Blue like ORVEX blue. A logo design perhaps a play of VN, K with a dangling T (colour can be any)
Nice to have
• I want a clean crisp card, not too busy, easy to read.

```html
<!DOCTYPE html>
<html lang="en">
<head>
<meta charset="utf-8">
<title>VelmoraNet Business Card</title>
<link rel="stylesheet" href="https://fonts.googleapis.com/css2?family=Open+Sans:wght@400;600;700;800&display=swap">
<style>
  :root {
    --brand-blue: #1f5fae;
    --brand-red: #d8262c;
    --card-white: #ffffff;
    --backdrop: #e6e6e6;
    --rule: #c9c9ee;
    --card-shadow: rgba(0, 0, 0, 0.18);
  }
  * { margin: 0; padding: 0; box-sizing: border-box; }
  html, body {
    width: 1200px;
    height: 900px;
    overflow: hidden;
    background: var(--backdrop);
    font-family: "Open Sans", sans-serif;
  }
  .canvas {
    width: 1200px;
    height: 900px;
    display: flex;
    flex-direction: column;
    align-items: center;
    justify-content: center;
    gap: 56px;
  }
  .card {
    position: relative;
    width: 600px;
    height: 343px;
    background: var(--card-white);
    box-shadow: 0 6px 18px var(--card-shadow);
  }
  .wordmark {
    display: flex;
    align-items: center;
    gap: 10px;
    color: var(--brand-blue);
    font-weight: 800;
    letter-spacing: -0.5px;
    line-height: 1;
  }
  .wordmark-dot {
    width: 16px;
    height: 16px;
    border-radius: 50%;
    background: var(--brand-red);
  }
  .card-front .wordmark {
    position: absolute;
    left: 50%;
    top: 50%;
    transform: translate(-50%, -50%);
    font-size: 52px;
  }
  .card-back .wordmark {
    position: absolute;
    right: 48px;
    top: 58px;
    font-size: 40px;
  }
  .card-back .wordmark-dot { width: 13px; height: 13px; }
  .holder {
    position: absolute;
    left: 36px;
    top: 146px;
  }
  .holder-name {
    color: var(--brand-blue);
    font-weight: 700;
    font-size: 17px;
    line-height: 1.2;
  }
  .holder-title {
    color: var(--brand-red);
    font-size: 13.5px;
    line-height: 1.3;
  }
  .divider {
    position: absolute;
    left: 240px;
    right: 36px;
    top: 176px;
    height: 1px;
    background: var(--rule);
  }
  .company-address {
    position: absolute;
    right: 36px;
    bottom: 34px;
    text-align: right;
    font-style: normal;
    color: var(--brand-red);
    font-size: 15.5px;
    line-height: 1.32;
  }
  .company-name {
    color: var(--brand-blue);
    font-weight: 700;
    font-size: 16.5px;
  }
</style>
</head>
<body>
  <main class="canvas">
    <section class="card card-front" aria-label="Business card front">
      <div class="wordmark"><span>VelmoraNet</span><span class="wordmark-dot"></span></div>
    </section>

    <section class="card card-back" aria-label="Business card back">
      <div class="wordmark"><span>VelmoraNet</span><span class="wordmark-dot"></span></div>
      <div class="holder">
        <p class="holder-name">Roshan Adeel</p>
        <p class="holder-title">Managing Director</p>
      </div>
      <div class="divider"></div>
      <address class="company-address">
        <span class="company-name">Velmora Net</span><br>
        Sdn. Bhd.5th Floor, Block D<br>
        Wisma PLB,No.14 Jalan Seri Melor<br>
        50470, Kuala Lumpur<br>
        Malaysia
      </address>
    </section>
  </main>
</body>
</html>
```